Redesign This Psychology Website

We would like a slight redesign of this successful psychology (relationship counselling) website:

www.TheKelvaleClinic.com.au

We are updating the website, and we'd like a slight refresh of the design and style.

Please keep to very similar colours, and use the same logo. We're looking for around 10 page templates, however the main one is the home page.

Keep in mind, this website already converts quite well, so we want a new, fresh design in keeping with this one. Please don't bother designing something too extremely different.

thanks :)

Target Market(s)

couples who are looking for relationship counselling. Men and women, 25 - 70, across Australia

Industry/Entity Type

Psychology

Number of Pages Required

5+ page

Font styles to use
Sans Serif

Colors
87cfc6
b7a5cd
ec1f27
ffffff
cee9f5

Requirements
Must have
• a similar look to the current design, just looking for a slight refresh.
• Search bar
• Areas for lots of photos
• same logo
• lots of content areas
Nice to have
• great content areas, where we can display a lot of content and our areas.
Should not have
• no colors like orange, etc.
• should not have a totally different feel.

```html
<!DOCTYPE html>
<html lang="en">
<head>
<meta charset="utf-8">
<title>The Kelvale Clinic – Relationship Counselling</title>
<link href="https://fonts.googleapis.com/css2?family=Open+Sans:wght@400;600;700;800&display=swap" rel="stylesheet">
<style>
:root{
  --teal:#87cfc6;
  --teal-deep:#4fb3ab;
  --teal-btn:#2ea6b3;
  --purple:#b7a5cd;
  --purple-soft:#c9bcdc;
  --red:#ec1f27;
  --sky:#cee9f5;
  --white:#ffffff;
  --ink:#4a4a4a;
  --muted:#777;
  --line:#d9d9d9;
  --card:#f5f5f7;
}
*{box-sizing:border-box;margin:0;padding:0}
html,body{width:1200px;height:4265px;overflow:hidden}
body{position:relative;background:var(--white);font-family:"Open Sans",Arial,sans-serif;color:var(--ink);font-size:14px}
.abs{position:absolute}
.ph{display:block}

/* header */
.brand{left:100px;top:18px;display:flex;align-items:center;gap:12px}
.brand-dot{width:58px;height:58px;border-radius:50%;background:var(--red)}
.brand-name{font-size:34px;font-weight:700;color:var(--teal-deep);line-height:1}
.brand-tag{left:172px;top:70px;font-size:13px;color:var(--red);font-weight:600}
.social{display:flex;gap:8px}
.social span{width:26px;height:26px;border-radius:50%;display:block}
.top-social{left:690px;top:14px}
.call{left:860px;top:16px;font-size:15px;font-weight:700;color:var(--teal-btn);display:flex;align-items:center;gap:8px}
.subnav{left:570px;top:66px;display:flex;gap:12px;align-items:center;font-size:11px;color:var(--teal-btn);font-weight:600}
.subnav .join{background:var(--sky);padding:5px 10px}
.mainnav{left:0;top:108px;width:1200px;height:57px;background:linear-gradient(var(--sky),#e2f2f9)}
.mainnav ul{list-style:none;display:flex;gap:42px;position:absolute;left:130px;top:19px;font-size:14px;color:var(--teal-btn)}
.search{position:absolute;left:888px;top:14px;width:208px;height:30px;background:var(--white);display:flex;align-items:center;justify-content:space-between;padding:0 10px;font-size:12px;color:#999}
.catnav{left:0;top:165px;width:1200px;height:48px;background:var(--purple)}
.catnav ul{list-style:none;display:flex;justify-content:space-between;position:absolute;left:135px;right:115px;top:15px;font-size:14px;color:var(--white)}

/* hero */
.hero{left:0;top:213px;width:1200px;height:447px;background:linear-gradient(180deg,#e9d3a0 0%,#c99a55 55%,#7a5a2c 100%)}
.hero-quote{position:absolute;left:0;width:1200px;top:200px;text-align:center;color:var(--white);font-size:34px;font-weight:600;line-height:1.25}
.hero-btns{position:absolute;top:287px;left:0;width:1200px;display:flex;justify-content:center;gap:10px}
.hero-btns span{background:var(--teal-btn);color:var(--white);font-weight:700;font-size:15px;padding:8px 22px}
.hero-arrows{position:absolute;left:122px;top:390px;display:flex;gap:4px}
.arrow{width:20px;height:20px;background:var(--white);display:flex;align-items:center;justify-content:center;border:1px solid var(--line)}

/* service cards */
.services{left:100px;top:671px;width:1000px;display:flex;gap:13px}
.svc{width:240px;height:409px;background:var(--white);border:1px solid var(--line);box-shadow:0 2px 6px rgba(0,0,0,.1);position:relative}
.svc .ph{height:196px}
.svc h3{font-size:17px;font-weight:600;color:var(--teal-btn);margin:14px 12px 4px;line-height:1.25}
.svc .need{font-size:12px;color:var(--red);font-weight:700;margin:0 12px 8px}
.svc p{font-size:12px;color:var(--muted);margin:0 12px;line-height:1.5}
.btn-more{display:inline-block;background:var(--purple);color:var(--white);font-size:11px;padding:5px 12px}
.svc .btn-more{position:absolute;left:12px;bottom:18px}

/* finder */
.finder{left:105px;top:1131px;width:990px;height:182px;background:linear-gradient(90deg,var(--purple-soft),var(--purple));border-top:3px solid #a592c0}
.finder-mark{position:absolute;left:92px;top:30px;width:60px;height:60px;border-radius:50%;background:var(--white);opacity:.9}
.finder h2{position:absolute;left:0;width:990px;top:42px;text-align:center;font-size:25px;font-weight:600;color:var(--white)}
.finder-form{position:absolute;left:115px;top:93px;display:flex;gap:12px}
.finder-form span{background:var(--white);height:32px;font-size:12px;color:#999;padding:8px 10px}
.finder-form .go{background:var(--red);color:var(--white);font-weight:700;width:98px;text-align:center}

/* specialise */
.section-title{font-size:25px;font-weight:600;color:var(--teal-deep);line-height:1.25}
.special{left:128px;top:1350px;width:520px}
.special p{font-size:13px;line-height:1.55;color:var(--ink);margin-top:16px}
.special .btn-more{margin-top:16px;background:var(--teal)}
.special-img{left:677px;top:1364px;width:389px;height:307px;background:linear-gradient(135deg,#d8c3ac,#8d6b55 60%,#f0e6dc)}

/* headers with rules */
.rule-head{left:128px;width:947px;display:flex;align-items:center;gap:12px}
.rule-head .section-title{white-space:nowrap}
.rule-head .rule{flex:1;height:1px;background:var(--line)}
.rule-head .arrows{display:flex;gap:4px}
.sub{font-size:14px;color:var(--ink);margin-top:2px}

.thumbs{left:128px;top:1797px;width:947px;display:flex;gap:22px}
.thumbs .ph{width:220px;height:159px}

/* blog */
.blog{left:128px;top:2067px;width:947px;display:flex;gap:32px}
.post{width:294px;height:469px;background:var(--card);position:relative;text-align:center}
.post .ph{height:220px}
.date{position:absolute;left:10px;top:0;width:62px;height:82px;background:var(--white);text-align:center;padding-top:8px;box-shadow:0 1px 4px rgba(0,0,0,.15)}
.date b{display:block;font-size:24px;line-height:1;color:#333}
.date span{display:block;font-size:13px;font-weight:700;color:var(--white);background:var(--red);margin:4px 0 2px}
.date i{font-style:normal;font-size:11px;font-weight:700}
.post h4{font-size:15px;font-weight:700;color:#333;margin:30px 24px 16px;line-height:1.3}
.post p{font-size:12px;color:var(--ink);margin:0 22px;line-height:1.75}
.post .btn-more{position:absolute;left:50%;transform:translateX(-50%);bottom:28px;background:var(--teal)}

/* videos */
.videos{left:128px;top:2664px;width:947px;display:flex;gap:28px}
.video{height:307px;position:relative}
.video.a{width:455px;background:linear-gradient(135deg,#d9d4cf,#9a8f88)}
.video.b{width:464px;background:linear-gradient(135deg,#e7e2dc,#b1a79f)}
.play{position:absolute;left:50%;top:50%;transform:translate(-50%,-50%)}

/* psychologists */
.team{left:128px;top:3000px;width:947px}
.team-text{position:absolute;left:0;top:52px;width:530px;font-size:13px;line-height:1.5}
.team-text p+p{margin-top:10px}
.common{position:absolute;left:560px;top:44px;width:387px}
.common h5{font-size:15px;font-weight:700;color:var(--teal-deep);margin-bottom:8px}
.common ul{list-style:none;columns:2;column-gap:16px;font-size:11px;line-height:1.6}
.common li::before{content:"";display:inline-block;width:5px;height:5px;background:var(--ink);border-radius:50%;margin-right:8px;vertical-align:middle}

/* approach */
.approach-img{left:128px;top:3312px;width:390px;height:321px;background:linear-gradient(135deg,#e8e6e2,#a9a095 60%,#d9d1c6)}
.approach{left:549px;top:3312px;width:526px}
.approach p{font-size:13px;line-height:1.55;margin-top:14px}
.approach .btn-more{margin-top:16px;background:var(--teal)}

/* promos */
.promos{left:128px;top:3687px;width:947px;display:flex;gap:28px}
.promo{height:131px;background:#ececec;display:flex;align-items:center;gap:16px;padding-left:10px;width:455px}
.promo + .promo{width:464px}
.promo .ph{width:110px;height:110px}
.promo small{display:block;font-size:15px;color:var(--ink)}
.promo strong{display:block;font-size:30px;font-weight:800;color:var(--red);line-height:1.1}
.promo em{font-style:normal;font-size:14px;color:var(--ink)}

/* login */
.login{left:105px;top:3852px;width:990px;height:105px;background:var(--red);border-bottom:6px solid #c8141b;display:flex;align-items:center;padding-left:82px;gap:18px}
.login h6{font-size:20px;font-weight:700;color:var(--white);margin-right:6px}
.login span{background:var(--white);height:38px;width:236px;font-size:12px;color:#999;padding:11px 10px}
.login .go{width:118px;background:var(--teal);color:var(--white);font-weight:700;text-align:center}

/* footer */
.footer{left:0;top:3957px;width:1200px;height:279px;background:var(--sky)}
.footer h6{position:absolute;left:135px;top:58px;font-size:20px;font-weight:700;color:var(--teal-deep)}
.fcol{position:absolute;top:100px;list-style:none;font-size:14px;line-height:1.65;color:var(--ink)}
.fcol li::before{content:"›";color:var(--teal-deep);margin-right:10px}
.f-dot{position:absolute;left:972px;top:68px;width:56px;height:56px;border-radius:50%;background:var(--red)}
.f-social{position:absolute;left:948px;top:140px}
.copy{left:0;top:4236px;width:1200px;height:29px;background:#b7dcec;text-align:center;font-size:11px;line-height:29px;color:var(--ink)}
</style>
</head>
<body>

<header>
  <div class="abs brand"><span class="brand-dot"></span><span class="brand-name">The Kelvale Clinic</span></div>
  <div class="abs brand-tag">helping you create loving relationships</div>
  <div class="abs social top-social"><span style="background:#2f4f9a"></span><span style="background:#2ea6b3"></span><span style="background:var(--red)"></span><span style="background:#b07c3c"></span></div>
  <div class="abs call">
    <svg width="16" height="16" viewBox="0 0 24 24"><path fill="currentColor" d="M6.6 10.8a15 15 0 0 0 6.6 6.6l2.2-2.2c.3-.3.7-.4 1-.2 1.1.4 2.3.6 3.6.6.6 0 1 .4 1 1V20c0 .6-.4 1-1 1A17 17 0 0 1 3 4c0-.6.4-1 1-1h3.5c.6 0 1 .4 1 1 0 1.3.2 2.5.6 3.6.1.3 0 .7-.2 1z"/></svg>
    CALL US ON : 1-300 555 014</div>
  <div class="abs subnav"><span class="join">JOIN OUR ASSOCIATE PROGRAM</span><span>MARRIAGE COUNSELLING</span><span>|</span><span>RELATIONSHIP COUNSELLING</span></div>
</header>

<nav class="abs mainnav">
  <ul><li>Home</li><li>About</li><li>Resources</li><li>Blog</li><li>Shop</li><li>Cart</li></ul>
  <div class="search">Search
    <svg width="14" height="14" viewBox="0 0 24 24"><circle cx="10" cy="10" r="7" fill="none" stroke="#2ea6b3" stroke-width="3"/><path d="M15 15l6 6" stroke="#2ea6b3" stroke-width="3"/></svg></div>
</nav>
<nav class="abs catnav">
  <ul><li>Counselling Types</li><li>Relationship Counselling Locations</li><li>Sex Theraphy Locations</li><li>Quizzes</li><li>F. A. Q´s</li><li>Contact Us</li></ul>
</nav>

<section class="abs hero" role="img" aria-label="Photo of a smiling couple sitting in a golden field at sunset">
  <p class="hero-quote">“ At the end of our life, what matters<br>most is how well did we love”</p>
  <div class="hero-btns"><span>COUNSELLING</span><span>RESOURCES</span><span>CONNECT US</span><span>LEARN MORE</span></div>
  <div class="hero-arrows">
    <span class="arrow"><svg width="8" height="10" viewBox="0 0 8 10"><path d="M6 1L2 5l4 4" stroke="#666" fill="none" stroke-width="1.6"/></svg></span>
    <span class="arrow"><svg width="8" height="10" viewBox="0 0 8 10"><path d="M2 1l4 4-4 4" stroke="#666" fill="none" stroke-width="1.6"/></svg></span>
  </div>
</section>

<section class="abs services">
  <article class="svc">
    <div class="ph" role="img" aria-label="Black and white photo of a worried woman" style="background:linear-gradient(135deg,#d0d0d0,#6f6f6f)"></div>
    <h3>Relationship Counselling</h3><div class="need">Do you need help with:</div>
    <p>Communication, Recovering from an affair, Loss of intimacy &amp; love, Power battles, Feeling like friends, not lovers</p>
    <span class="btn-more">Read more</span>
  </article>
  <article class="svc">
    <div class="ph" role="img" aria-label="Photo of a couple resting together in bed" style="background:linear-gradient(135deg,#e6e6e6,#9c9c9c)"></div>
    <h3>Sex Theraphy Counselling</h3><div class="need">Do you need help with:</div>
    <p>Low libido, Erectile difficulties, Premature ejaculation, Differing libidos, Porn addiction, Keeping sex exciting</p>
    <span class="btn-more">Read more</span>
  </article>
  <article class="svc">
    <div class="ph" role="img" aria-label="Photo of an upset couple after an argument" style="background:linear-gradient(135deg,#d8d3cd,#8a8580)"></div>
    <h3>Anger Management Counselling</h3><div class="need">Do you need help with:</div>
    <p>Managing angry outbursts, expressing your anger in healthy ways</p>
    <span class="btn-more">Read more</span>
  </article>
  <article class="svc">
    <div class="ph" role="img" aria-label="Photo of a couple sitting apart on a sofa" style="background:linear-gradient(135deg,#efe7dd,#b9a998)"></div>
    <h3>Narcissism Counselling</h3><div class="need">Do you need help with:</div>
    <p>Managing narcissistic, superior, entitled, arrogant and lack of empathy tendencies in you or your partner</p>
    <span class="btn-more">Read more</span>
  </article>
</section>

<section class="abs finder">
  <span class="finder-mark"></span>
  <h2>Find Our Psychologist Near You</h2>
  <div class="finder-form"><span style="width:200px">Type of Counselling</span><span style="width:200px">Location</span><span style="width:200px">Postcode</span><span class="go">Search</span></div>
</section>

<section class="abs special">
  <h2 class="section-title">We Specialise in Relationship &amp;<br>Marriage Counselling</h2>
  <p>At the Kelvale Clinic, we are a group of PSYCHOLOGISTS, Australia wide who are passionate about relationships and helping you with yours.</p>
  <p>Our vision is to provide the most highly regarded and comprehensive marriage counselling and relationship counselling, and sex therapy in Australia, at reasonable and affordable rates.</p>
  <p>When we are experiencing relationship and marriage problems, there can be a lot of pain and confusion, and it can often be difficult to cope with the other areas of our lives when we are struggling with problems with our partner.</p>
  <span class="btn-more">Read more</span>
</section>
<div class="abs special-img" role="img" aria-label="Photo of a laughing couple embracing"></div>

<div class="abs rule-head" style="top:1735px"><h2 class="section-title">Photos and Videos</h2><span class="rule"></span>
  <span class="arrows"><span class="arrow"><svg width="8" height="10" viewBox="0 0 8 10"><path d="M6 1L2 5l4 4" stroke="#666" fill="none" stroke-width="1.6"/></svg></span><span class="arrow"><svg width="8" height="10" viewBox="0 0 8 10"><path d="M2 1l4 4-4 4" stroke="#666" fill="none" stroke-width="1.6"/></svg></span></span></div>
<section class="abs thumbs">
  <div class="ph" role="img" aria-label="Photo of a happy couple outdoors" style="background:linear-gradient(135deg,#f0c890,#b5754a)"></div>
  <div class="ph" role="img" aria-label="Photo of a couple hugging in the city" style="background:linear-gradient(135deg,#e8dccf,#9b7a65)"></div>
  <div class="ph" role="img" aria-label="Video still of a couple with a chalk heart drawing" style="background:linear-gradient(135deg,#4a4a4a,#1f1f1f)"></div>
  <div class="ph" role="img" aria-label="Photo of a couple lying in bed smiling" style="background:linear-gradient(135deg,#f5efe8,#c9b39f)"></div>
</section>

<div class="abs rule-head" style="top:1995px"><div><h2 class="section-title">Blog</h2><div class="sub">Relationships &amp; Sex</div></div><span class="rule"></span>
  <span class="arrows"><span class="arrow"><svg width="8" height="10" viewBox="0 0 8 10"><path d="M6 1L2 5l4 4" stroke="#666" fill="none" stroke-width="1.6"/></svg></span><span class="arrow"><svg width="8" height="10" viewBox="0 0 8 10"><path d="M2 1l4 4-4 4" stroke="#666" fill="none" stroke-width="1.6"/></svg></span></span></div>
<section class="abs blog">
  <article class="post">
    <div class="ph" role="img" aria-label="Photo of two smiling men" style="background:linear-gradient(135deg,#e2d6c8,#8d7461)"></div>
    <div class="date"><b>05</b><span>FEB</span><i>2017</i></div>
    <h4>Duis aute irure dolor in reprehenderit in voluptate</h4>
    <p>Duis aute irure dolor in reprehenderit in voluptate velit esse cillum dolore eu fugiat nulla pariatur. Excepteur sint occaecat cupidatat ...</p>
    <span class="btn-more">Read more</span>
  </article>
  <article class="post">
    <div class="ph" role="img" aria-label="Photo of a couple hugging in winter clothes" style="background:linear-gradient(135deg,#d7d7d7,#8b8b8b)"></div>
    <div class="date"><b>05</b><span>FEB</span><i>2017</i></div>
    <h4>Duis aute irure dolor in reprehenderit in voluptate</h4>
    <p>Duis aute irure dolor in reprehenderit in voluptate velit esse cillum dolore eu fugiat nulla pariatur. Excepteur sint occaecat cupidatat ...</p>
    <span class="btn-more">Read more</span>
  </article>
  <article class="post">
    <div class="ph" role="img" aria-label="Photo of an older couple smiling together" style="background:linear-gradient(135deg,#f0d9b8,#b58c5e)"></div>
    <div class="date"><b>05</b><span>FEB</span><i>2017</i></div>
    <h4>Duis aute irure dolor in reprehenderit in voluptate</h4>
    <p>Duis aute irure dolor in reprehenderit in voluptate velit esse cillum dolore eu fugiat nulla pariatur. Excepteur sint occaecat cupidatat ...</p>
    <span class="btn-more">Read more</span>
  </article>
</section>

<div class="abs rule-head" style="top:2580px"><div><h2 class="section-title">Videos</h2><div class="sub">What To Expect From Counselling</div></div><span class="rule"></span></div>
<section class="abs videos">
  <div class="video a" role="img" aria-label="Video still of a psychologist speaking to camera">
    <svg class="play" width="58" height="58" viewBox="0 0 58 58"><circle cx="29" cy="29" r="29" fill="#333" opacity=".85"/><path d="M23 17l17 12-17 12z" fill="#fff"/></svg></div>
  <div class="video b" role="img" aria-label="Video still of a couple in a counselling session">
    <svg class="play" width="58" height="58" viewBox="0 0 58 58"><circle cx="29" cy="29" r="29" fill="#333" opacity=".85"/><path d="M23 17l17 12-17 12z" fill="#fff"/></svg></div>
</section>

<section class="abs team">
  <div class="rule-head" style="position:static;width:947px"><h2 class="section-title">Our Kelvale Relationship Psychologists</h2><span class="rule"></span></div>
  <div class="team-text">
    <p>Our team of 75 hand chosen Registered Psychologists in 61 locations Australia wide, are individually selected for their knowledge, experience, compassion, and unbiased approach to marriage counselling and sexual therapy.<br>In addition all our Psychologists take part in our initial Relationship Counselling Methodologies Training and yearly In-house conferences, ensuring you are in safe and experienced hands.</p>
    <p>As we are Psychologists, you may be eligible for Medicare &amp; Private Health Insurance Rebates.<br>We are highly experienced and can help you with all kinds of relationship difficulties.</p>
  </div>
  <div class="common">
    <h5>Here are some of the common ones:</h5>
    <ul>
      <li>Affairs</li><li>Controlling behaviour</li><li>Verbal abuse</li><li>Imbalance of power</li><li>Lack of intimacy</li><li>Poor communication</li><li>Loss of love</li><li>Relationship neglect</li><li>Sexual problems</li>
      <li>Problems from childhood</li><li>Problems with parenting your children</li><li>Step children and in-laws</li><li>All forms of family problems</li><li>Anger management problems</li><li>Porn addiction problems</li><li>Pre-marriage programs</li><li>Narcissism problems</li>
    </ul>
  </div>
</section>

<div class="abs approach-img" role="img" aria-label="Photo of a couple talking with a counsellor"></div>
<section class="abs approach">
  <h2 class="section-title">Our Relationship Counselling Approach</h2>
  <p>It is an important part of our policy to take a very positive approach to our relationship counselling.</p>
  <p>We feel it is important to really understand the problems and perspectives of each of you, and at the same time, we find that most couples are looking to find a positive action plan and way through their problems to make changes which have a positive impact and a real sense of hope for their relationship.</p>
  <p>Read more about our approach to counselling in our relationship counselling sessions, and frequently asked questions about the relationship and marriage counselling process.</p>
  <span class="btn-more">Read more</span>
</section>

<section class="abs promos">
  <div class="promo"><div class="ph" role="img" aria-label="Portrait photo of the psychologist" style="background:linear-gradient(135deg,#f1d6a5,#c7925a)"></div>
    <div><small>Find Out More</small><strong>ABOUT US</strong><em>Marnie Psychologist Gold Coast</em></div></div>
  <div class="promo"><div class="ph" role="img" aria-label="Photo of a smiling couple" style="background:linear-gradient(135deg,#f3dfcf,#b98a6d)"></div>
    <div><small>Take Our</small><strong>KELVALE RELATIONSHIP</strong><em>Assessment</em></div></div>
</section>

<section class="abs login">
  <h6>Member Login</h6><span>Email</span><span>Password</span><span class="go">Submit</span>
</section>

<footer class="abs footer">
  <h6>Quick Links</h6>
  <ul class="fcol" style="left:135px"><li>Home</li><li>About Us</li><li>Resources</li><li>Blog</li><li>Shop</li><li>Cart</li></ul>
  <ul class="fcol" style="left:305px"><li>Counselling Types</li><li>Relationship Counselling Locations</li><li>Sex Theraphy Locations</li><li>Quizzes</li><li>F. A. Q´s</li><li>Contact Us</li></ul>
  <ul class="fcol" style="left:632px"><li>Privacy Policy</li><li>Terms &amp; Conditions</li><li>Site Map</li><li>Associate Psychologists Program</li></ul>
  <span class="f-dot"></span>
  <div class="social f-social"><span style="background:#2f4f9a"></span><span style="background:#2ea6b3"></span><span style="background:var(--red)"></span><span style="background:#b07c3c"></span></div>
</footer>
<div class="abs copy">Copyrights © 2017. www.kelvalesite.com. All Rights Reserved.</div>

</body>
</html>
```